business card - for laser marking

I need design (curve) for my business card (make with laser) size 85mm x 55mm. How it look business card with laser marking see attached picture.

color:
Background: white
text and icons black

Please include: one side
1. dominik vrabec - direktor
2. phone: +386(0)41 726 190
+386(0)580 237 61
3. info@zarezko.example
4. faecebook.com/Zarezko.Ex
5. KM-ATELJE, Dominik Vrabec s.p.
Lipova ulica 19, 1000 Ljubljana, SI
6. logo

Please include: second side
1. logo
2. www.zarezko.example
3. Lasersko graviranje
ovitki telefonov, ohišja telefonov / tablic, nakit, ure, alu vizitke, dog-tagi, kemični svinčniki, orodja, noži, vžigalniki

Industry/Entity Type

Business

Contact Information for Business Card

Please include: one side
+386(0)580 237 61
3. info@zarezko.example
6. logo

1. logo
2. www.zarezko.example
3. Lasersko graviranje

Colors
000000
ffffff

Requirements
Must have
• I need design (curve) for my business card (make with laser) size 85mm x 55mm. How it look business card with laser marking see attached picture.
• color:
• Background: white
• text and icons black
• Please include: one side
• 1. dominik vrabec - direktor
• 2. phone: +386(0)41 726 190
• +386(0)580 237 61
• 3. info@zarezko.example
• 4. faecebook.com/Zarezko.Ex
• 5. KM-ATELJE, Dominik Vrabec s.p.
• Lipova ulica 19, 1000 Ljubljana, SI
• 6. logo
• Please include: second side
• 1. logo
• 2. www.zarezko.example
• 3. Lasersko graviranje
• ovitki telefonov, ohišja telefonov / tablic, nakit, ure, alu vizitke, dog-tagi, kemični svinčniki, orodja, noži, vžigalniki

```html
<!DOCTYPE html>
<html lang="sl">
<head>
<meta charset="utf-8">
<title>Zarezko – vizitka</title>
<link rel="stylesheet" href="https://fonts.googleapis.com/css2?family=Roboto:wght@400;700&family=Roboto+Condensed:wght@700&display=swap">
<style>
  :root {
    --backdrop: #5b3f2c;
    --card: #1f2022;
    --ink: #f2f2f2;
    --accent-pink: #c9164b;
    --accent-green: #5c9c2f;
    --rule: #8a8b8d;
  }
  * { margin: 0; padding: 0; box-sizing: border-box; }
  html, body { width: 1200px; height: 960px; overflow: hidden; }
  body {
    background: var(--backdrop);
    position: relative;
    font-family: "Roboto", Arial, sans-serif;
    color: var(--ink);
  }
  .card {
    position: absolute;
    background: var(--card);
    overflow: hidden;
  }
  .card--front { left: 314px; top: 113px; width: 601px; height: 342px; }
  .card--back { left: 312px; top: 472px; width: 599px; height: 343px; }

  /* Front */
  .name-marker {
    position: absolute; left: 0; top: 177px; width: 13px; height: 28px;
    background: var(--accent-pink);
  }
  .person-name {
    position: absolute; left: 36px; top: 174px;
    font-family: "Roboto Condensed", Arial, sans-serif;
    font-weight: 700; font-size: 20px; letter-spacing: 0.2px;
    color: var(--accent-pink);
  }
  .person-role {
    position: absolute; left: 36px; top: 200px;
    font-family: "Roboto Condensed", Arial, sans-serif;
    font-weight: 700; font-size: 15px;
    color: var(--accent-green);
  }
  .divider {
    position: absolute; left: 36px; top: 226px; width: 530px; height: 1px;
    background: var(--rule);
  }
  .contact-list {
    position: absolute; left: 36px; top: 238px; list-style: none;
  }
  .contact-item {
    display: flex; align-items: center; height: 19px;
    font-size: 14px; line-height: 19px;
  }
  .contact-icon {
    width: 12px; height: 12px; margin-right: 10px; flex: none;
    fill: var(--accent-pink);
  }
  .company-address {
    position: absolute; right: 33px; top: 241px;
    text-align: right; font-size: 14px; line-height: 19px; font-style: normal;
  }
  .brand-front {
    position: absolute; left: 400px; top: 100px; width: 170px;
    display: flex; align-items: center; justify-content: center; gap: 8px;
  }
  .brand-dot {
    width: 12px; height: 12px; border-radius: 50%; background: var(--accent-green);
  }
  .brand-name {
    font-weight: 700; font-size: 26px; letter-spacing: 1px;
    color: var(--accent-pink);
  }

  /* Back */
  .brand-back {
    position: absolute; left: 0; right: 0; top: 144px;
    text-align: center;
    font-weight: 700; font-size: 44px; letter-spacing: 2px;
    color: var(--accent-pink);
  }
  .services {
    position: absolute; left: 0; right: 0; top: 226px;
    text-align: center; font-size: 14px; line-height: 18.5px;
  }
  .website {
    position: absolute; left: 0; right: 0; top: 302px;
    text-align: center; font-weight: 700; font-size: 15px;
    color: var(--accent-pink);
  }
  .website .domain { color: var(--accent-green); }
</style>
</head>
<body>

<section class="card card--front" aria-label="Sprednja stran vizitke">
  <div class="brand-front">
    <span class="brand-dot"></span>
    <span class="brand-name">ZAREZKO</span>
  </div>

  <span class="name-marker"></span>
  <h1 class="person-name">DOMINIK VRABEC</h1>
  <p class="person-role">DIREKTOR</p>
  <div class="divider"></div>

  <ul class="contact-list">
    <li class="contact-item">
      <svg class="contact-icon" viewBox="0 0 24 24" aria-hidden="true"><path d="M6.6 10.8a15.1 15.1 0 0 0 6.6 6.6l2.2-2.2c.3-.3.7-.4 1-.2 1.1.4 2.3.6 3.6.6.6 0 1 .4 1 1V20c0 .6-.4 1-1 1A17 17 0 0 1 3 4c0-.6.4-1 1-1h3.5c.6 0 1 .4 1 1 0 1.3.2 2.5.6 3.6.1.3 0 .7-.2 1z"/></svg>
      +386(0)580 237 61
    </li>
    <li class="contact-item">
      <svg class="contact-icon" viewBox="0 0 24 24" aria-hidden="true"><path d="M7 1h10a2 2 0 0 1 2 2v18a2 2 0 0 1-2 2H7a2 2 0 0 1-2-2V3a2 2 0 0 1 2-2zm0 3v14h10V4zm5 15.5a1 1 0 1 0 0 2 1 1 0 0 0 0-2z"/></svg>
      +386(0)41 726 190
    </li>
    <li class="contact-item">
      <svg class="contact-icon" viewBox="0 0 24 24" aria-hidden="true"><path d="M2 5h20v14H2zm2 2v.5l8 5 8-5V7l-8 5z"/></svg>
      info@zarezko.example
    </li>
    <li class="contact-item">
      <svg class="contact-icon" viewBox="0 0 24 24" aria-hidden="true"><rect x="2" y="2" width="20" height="20" rx="2"/></svg>
      Zarezko.Ex
    </li>
  </ul>

  <address class="company-address">
    KM-ATELJE<br>
    Dominik Vrabec s.p.<br>
    Lipova ulica 19<br>
    1000 Ljubljana, SI
  </address>
</section>

<section class="card card--back" aria-label="Zadnja stran vizitke">
  <h2 class="brand-back">ZAREZKO</h2>
  <p class="services">
    Lasersko graviranje<br>
    ovitki telefonov, ohišja telefonov / tablic, nakit, ure, alu vizitke<br>
    dog-tagi, kemicni svincniki, orodja, noži, vžigalniki
  </p>
  <p class="website">www.<span class="domain">zarezko</span>.example</p>
</section>

</body>
</html>
```